Professional & attention grabbing.

A business card design, front and back. I already have a logo I will attach, but I am open to something new as well.
Things to include:
Name:
Title:
Phone:
Email:
Wanting something that is professional but attention grabbing.
Also we do a lot of work using drones on natural gas pipelines (leading the future)if you want to include any of that. I'm open to ideas.
Target Market(s)
Natural gas transmission industry / greenhouse gas mitigation industry
Industry/Entity Type
Business
Colors
Designer to choose colors to be used in the design.
Look and feel
Each slider illustrates characteristics of the customer's brand and the style your logo design should communicate.

```html
<!DOCTYPE html>
<html lang="en">
<head>
<meta charset="utf-8">
<title>Ridgeline Inspections — Business Card</title>
<link href="https://fonts.googleapis.com/css2?family=Roboto:wght@400;500;700;900&display=swap" rel="stylesheet">
<style>
  :root {
    --stage: #5a5a5c;
    --card-dark: #2a2b2e;
    --card-dark-edge: #1b1c1e;
    --card-light: #ffffff;
    --red: #d4211f;
    --red-deep: #a8151a;
    --ink: #2b2b2d;
    --ink-soft: #4a4a4d;
    --rule: #b9b9bc;
    --white: #ffffff;
  }
  * { box-sizing: border-box; margin: 0; padding: 0; }
  html, body { width: 1200px; height: 852px; overflow: hidden; }
  body {
    background: var(--stage);
    font-family: "Roboto", Arial, sans-serif;
    position: relative;
  }
  .card {
    position: absolute;
    width: 540px;
    height: 308px;
    border-radius: 18px;
    overflow: hidden;
    box-shadow: 0 12px 30px rgba(0,0,0,.35);
  }

  /* Front (dark) */
  .card--front {
    left: 70px; top: 70px;
    background: linear-gradient(135deg, #3a3b3f 0%, var(--card-dark) 50%, var(--card-dark-edge) 100%);
  }
  .card--front .brand {
    position: absolute; left: 0; right: 0; top: 96px;
    display: flex; align-items: center; justify-content: center; gap: 14px;
  }
  .brand__square { width: 34px; height: 34px; background: var(--red); }
  .brand__name {
    font-weight: 900; font-size: 40px; letter-spacing: 1px; line-height: 1;
  }
  .card--front .brand__name { color: var(--white); }
  .card--front .band {
    position: absolute; left: 0; right: 0; bottom: 34px; height: 40px;
    background: linear-gradient(180deg, var(--red) 0%, var(--red-deep) 100%);
    display: flex; align-items: center; justify-content: center;
  }
  .band__text { color: var(--white); font-size: 15px; font-weight: 400; letter-spacing: .3px; }

  /* Back (light) */
  .card--back {
    left: 590px; top: 474px;
    background: var(--card-light);
  }
  .card--back .brand {
    position: absolute; left: 34px; top: 128px;
    display: flex; align-items: center; gap: 10px;
  }
  .card--back .brand__square { width: 22px; height: 22px; }
  .card--back .brand__name { color: var(--ink); font-size: 26px; }
  .divider {
    position: absolute; left: 268px; top: 58px; width: 1px; height: 150px; background: var(--rule);
  }
  .contact { position: absolute; left: 290px; top: 66px; }
  .contact__name { color: var(--red); font-weight: 900; font-size: 21px; letter-spacing: 1px; }
  .contact__title { color: var(--ink-soft); font-size: 12px; margin-top: 3px; margin-bottom: 12px; }
  .contact__list { list-style: none; }
  .contact__item {
    display: flex; align-items: center; gap: 8px;
    color: var(--ink); font-size: 12.5px; line-height: 20px;
  }
  .contact__icon { width: 12px; height: 12px; fill: var(--red); flex: none; }
  .tab {
    position: absolute; right: 0; bottom: 0; width: 250px; height: 58px;
    background: var(--red);
    display: flex; align-items: center; justify-content: center;
    clip-path: polygon(0 22%, 100% 0, 100% 100%, 0 100%);
  }
  .tab__text { color: var(--white); font-size: 13.5px; padding-top: 10px; }
  .base-strip {
    position: absolute; left: 0; bottom: 0; width: 300px; height: 18px;
    background: linear-gradient(90deg, #1f1f21, #3a3a3c);
  }
</style>
</head>
<body>

  <section class="card card--front" aria-label="Card front">
    <div class="brand">
      <span class="brand__square"></span>
      <span class="brand__name">RIDGELINE</span>
    </div>
    <div class="band">
      <p class="band__text">Also we do a lot of work using drones on natural gas pipelines</p>
    </div>
  </section>

  <section class="card card--back" aria-label="Card back">
    <div class="brand">
      <span class="brand__square"></span>
      <span class="brand__name">RIDGELINE</span>
    </div>
    <div class="divider"></div>
    <div class="contact">
      <h1 class="contact__name">DANIEL REEVES</h1>
      <p class="contact__title">Managing Director</p>
      <ul class="contact__list">
        <li class="contact__item">
          <svg class="contact__icon" viewBox="0 0 24 24"><path d="M6.6 10.8a15.1 15.1 0 0 0 6.6 6.6l2.2-2.2c.3-.3.7-.4 1-.2 1.1.4 2.3.6 3.6.6.6 0 1 .4 1 1V20c0 .6-.4 1-1 1A17 17 0 0 1 3 4c0-.6.4-1 1-1h3.5c.6 0 1 .4 1 1 0 1.3.2 2.5.6 3.6.1.3 0 .7-.2 1z"/></svg>
          1300 555 018
        </li>
        <li class="contact__item">
          <svg class="contact__icon" viewBox="0 0 24 24"><circle cx="12" cy="12" r="10"/><path d="M2 12h20M12 2c3 3 3 17 0 20M12 2c-3 3-3 17 0 20" stroke="#fff" stroke-width="1.6" fill="none"/></svg>
          www.ridgelineinspect.com
        </li>
        <li class="contact__item">
          <svg class="contact__icon" viewBox="0 0 24 24"><path d="M2 5h20v14H2z"/><path d="M2 5l10 8 10-8" stroke="#fff" stroke-width="1.8" fill="none"/></svg>
          daniel.reeves@ridgelineinspect.com
        </li>
      </ul>
    </div>
    <div class="base-strip"></div>
    <div class="tab"><p class="tab__text">Drones on natural gas pipelines</p></div>
  </section>

</body>
</html>
```